Tri Fold Brocure for Lumen Med Spa

Brochure for a med spa
www.lumenmedspas-example.com

we would like to use a clean white base layer with pops of greenery promoting a elegant high class customer service feel. Does not have to have only greenery could also use flower for pops of color. This need to have a elegant feel adn not overpower the message.

I have included my first rough draft, were just missing the mark, not vibrant or classy enough.

Target Market(s)

30-60 year old women
Higher income or wealth
men make up only about 20%

Font styles to use
Serif

Colors
0392cd
ffffff
acd036

Requirements
Must have
• 1. Contact information see example image for detail--instagram and FB address
• 2. An area for " ABOUT US" see example image
• 3. Memberships area
• 4. List of services
Nice to have
• Greenery and feeling of a new beginning or rejuvenation
• photos of women with feeling of rejuvenation
Should not have
• any massage photos or sense of a massage as we do not do this service

```html
<!DOCTYPE html>
<html lang="en">
<head>
<meta charset="utf-8">
<title>Lumen Med Spa – Menu &amp; Memberships</title>
<link rel="stylesheet" href="https://fonts.googleapis.com/css2?family=Open+Sans:wght@400;600;700&display=swap">
<style>
  :root {
    --backdrop: #3a3a3c;
    --paper: #ffffff;
    --blue: #1a74bf;
    --rule-blue: #2b6fb5;
    --green: #2eb34b;
    --ink: #111111;
    --leaf-dark: #1f6f1c;
    --leaf-mid: #3f9a2a;
    --leaf-light: #9fd34a;
  }
  * { margin: 0; padding: 0; box-sizing: border-box; }
  html, body { width: 1200px; height: 941px; overflow: hidden; background: var(--backdrop); }
  body { font-family: "Open Sans", Arial, sans-serif; color: var(--ink); position: relative; }

  .brochure-panel { position: absolute; left: 41px; top: 36px; width: 1118px; height: 869px; background: var(--paper); }
  .hero-photo { position: absolute; left: 54px; top: 47px; width: 1093px; height: 339px; }

  .menu { position: absolute; left: 80px; top: 382px; width: 290px; }
  .section-title { color: var(--blue); font-weight: 700; font-size: 32px; letter-spacing: 0.5px; line-height: 1.2; }
  .price-table { position: absolute; left: 7px; top: 46px; width: 275px; border-collapse: collapse; }
  .price-table th, .price-table td { font-weight: 700; font-size: 21px; height: 31.8px; padding: 0 0 0 1px; line-height: 1; }
  .price-table th { font-weight: 600; font-size: 24px; height: 40px; vertical-align: middle; }
  .price-table td { border-top: 1px solid var(--rule-blue); vertical-align: middle; }
  .price-table .col-service { width: 133px; border-right: 1px solid var(--rule-blue); }
  .price-table .col-price { text-align: right; padding-right: 4px; }
  .price-table th.col-price { padding-right: 14px; }

  .memberships { position: absolute; left: 444px; top: 352px; width: 330px; }
  .subhead { font-weight: 600; font-size: 19px; margin-top: 4px; }
  .intro { font-size: 12.7px; line-height: 16.6px; text-align: justify; margin-top: 6px; }
  .all-members { color: var(--blue); font-weight: 600; font-size: 13.2px; line-height: 16px; margin-top: 9px; letter-spacing: 0.3px; }

  .benefit-list { list-style: none; }
  .benefit-list li { position: relative; padding-left: 17px; font-weight: 600; font-size: 12.9px; line-height: 16px; }
  .benefit-list li::before { content: ""; position: absolute; left: 3px; top: 5px; width: 6px; height: 6px; border-radius: 50%; background: var(--green); }
  .benefit-list.loose li { margin-top: 10.3px; }
  .benefit-list.tight li { margin-top: 3.4px; }
  .memberships .benefit-list { margin-top: 7px; }

  .tiers { position: absolute; left: 805px; top: 296px; width: 320px; }
  .tier-name { color: var(--blue); font-weight: 600; font-size: 24px; line-height: 30px; }
  .tier-lead { font-weight: 600; font-size: 18.3px; line-height: 22.6px; margin-top: 3px; }
  .tiers .benefit-list.loose { margin-top: -2px; }
  .tiers .tier-lead.second { margin-top: 4px; }
  .tiers .benefit-list.tight { margin-top: -3px; }

  .footer-band { position: absolute; left: 54px; top: 859px; width: 1093px; height: 33px; background: var(--green); }
</style>
</head>
<body>
  <div class="brochure-panel"></div>

  <svg class="hero-photo" viewBox="0 0 1161 360" role="img" aria-label="Photo of a woman peeking through lush green tropical leaves">
    <defs>
      <linearGradient id="leafTone" x1="0" y1="0" x2="1" y2="1">
        <stop offset="0" stop-color="var(--leaf-mid)"/>
        <stop offset="0.45" stop-color="var(--leaf-dark)"/>
        <stop offset="0.8" stop-color="var(--leaf-mid)"/>
        <stop offset="1" stop-color="var(--leaf-light)"/>
      </linearGradient>
    </defs>
    <path d="M0 0 H1161 V330 C1030 262 920 212 773 218 C600 226 450 300 300 335 C200 356 80 352 0 345 Z" fill="url(#leafTone)"/>
  </svg>

  <section class="menu">
    <h2 class="section-title">MENU</h2>
    <table class="price-table">
      <thead><tr><th class="col-service">Service</th><th class="col-price">Price</th></tr></thead>
      <tbody>
        <tr><td class="col-service">Item</td><td class="col-price">00.00 $</td></tr>
        <tr><td class="col-service">Item</td><td class="col-price">00.00 $</td></tr>
        <tr><td class="col-service">Item</td><td class="col-price">00.00 $</td></tr>
        <tr><td class="col-service">Item</td><td class="col-price">00.00 $</td></tr>
        <tr><td class="col-service">Item</td><td class="col-price">00.00 $</td></tr>
        <tr><td class="col-service">Item</td><td class="col-price">00.00 $</td></tr>
        <tr><td class="col-service">Item</td><td class="col-price">00.00 $</td></tr>
        <tr><td class="col-service">Item</td><td class="col-price">00.00 $</td></tr>
        <tr><td class="col-service">Item</td><td class="col-price">00.00 $</td></tr>
        <tr><td class="col-service">Item</td><td class="col-price">00.00 $</td></tr>
        <tr><td class="col-service">Item</td><td class="col-price">00.00 $</td></tr>
        <tr><td class="col-service">Item</td><td class="col-price">00.00 $</td></tr>
      </tbody>
    </table>
  </section>

  <section class="memberships">
    <h2 class="section-title">MEMBERSHIPS</h2>
    <h3 class="subhead">Lumen Medspa Memberships</h3>
    <p class="intro">At Lumen Medspa we understand the quality of a great experience. We want you to get the best results from your visits, and truly enjoy your new beautiful self. Our exclusive membership benefits will bring a new peace of mind for you, and deliver the absolute best results for all of our services. We have two levels of membership, each with their own benefits. Many of our Medspa services require more than one visit. By paying for our monthly memberships you will be guaranteed the lowest price and the utmost attention.</p>
    <p class="all-members">All members receive great benefits through Lumen Medspa:</p>
    <ul class="benefit-list loose">
      <li>Guaranteed best deals and monthly specials</li>
      <li>Reward Points to use at Lumen Medspa</li>
      <li>Share with family or friends</li>
      <li>Fast and simple check out</li>
      <li>Membership pricing on each service</li>
      <li>Flexible payment options</li>
      <li>And of course you get the ultimate satisfaction with your true image of yourself.</li>
    </ul>
  </section>

  <section class="tiers">
    <h2 class="tier-name">Refresh Membership:<br>$149/month</h2>
    <p class="tier-lead">Save money and feel great with the following benefits:</p>
    <ul class="benefit-list loose">
      <li>Basic Facials</li>
      <li>Basic Chemical Peels</li>
      <li>I.V. fluids and injectables</li>
      <li>30 min laser hair removal</li>
      <li>10% off all injectables</li>
      <li>$10 B12 vitamin shots</li>
      <li>10-15% off any additional services</li>
      <li>ReLumen Membership: $229/month</li>
    </ul>
    <p class="tier-lead second">Enjoy the most exclusive membership benefits:</p>
    <ul class="benefit-list tight">
      <li>Signature facial with IV fluids</li>
      <li>Signature chemical peels plus IV fluids</li>
      <li>Microneedling</li>
      <li>IPL photo facial</li>
      <li>1 hour Laser hair removal</li>
      <li>15% off all injectables</li>
      <li>$10 B12 vitamin shots</li>
      <li>$15 MIC shots</li>
      <li>10% off all care products</li>
      <li>10-15% off any additional services</li>
    </ul>
  </section>

  <div class="footer-band"></div>
</body>
</html>
```